Letter and Envelope Design For Harborline Realty

Please design a letter and an envelope incorporating our logo (See Attached). We are also launched a business card contest. Since we want them to match, please feel free to submit a design for both the business card and also the letter design and envelope.

Requirements
Must have
• The envelope, the letter and the business cards must match somehow connecting the designs. We want them to have something that holds them together besides the logo.

```html
<!DOCTYPE html>
<html lang="en">
<head>
<meta charset="utf-8">
<title>Harborline Realty Stationery</title>
<link rel="stylesheet" href="https://fonts.googleapis.com/css2?family=Lato:wght@400;700&family=Kaushan+Script&display=swap">
<style>
  :root {
    --navy: #2b2f7e;
    --ink: #555a60;
    --heading: #25406a;
    --backdrop: #bbbcbf;
    --paper: #ffffff;
    --paper-shade: #efefef;
    --rule: #c9cacc;
  }
  * { margin: 0; padding: 0; box-sizing: border-box; }
  html, body { width: 1200px; height: 484px; overflow: hidden; }
  body { background: var(--backdrop); font-family: "Lato", Arial, sans-serif; position: relative; }

  .sheet, .envelope, .card { position: absolute; background: var(--paper); overflow: hidden; }

  /* Brand lockup: ring + name */
  .brand { position: absolute; display: flex; flex-direction: column; align-items: center; }
  .brand-ring { border: 2px solid var(--navy); border-radius: 50%; background: var(--paper); }
  .brand-name { color: var(--navy); font-weight: 700; letter-spacing: .08em; text-transform: uppercase; white-space: nowrap; margin-top: 3px; }

  /* Letterhead */
  .letter { width: 322px; height: 416px; top: 38px; background: linear-gradient(180deg, var(--paper) 40%, var(--paper-shade)); }
  .letter--one { left: 33px; }
  .letter--two { left: 378px; }
  .letter .brand { left: 30px; top: 11px; width: 86px; }
  .letter .brand-ring { width: 32px; height: 32px; }
  .letter .brand-name { font-size: 7.4px; }
  .contact-list { position: absolute; list-style: none; font-size: 5.2px; color: var(--ink); line-height: 8px; }
  .contact-list li { display: flex; align-items: center; gap: 3px; }
  .contact-list svg { width: 5px; height: 5px; fill: var(--navy); }
  .letter--one .contact-list { left: 234px; top: 27px; border-left: 1px solid var(--rule); padding-left: 3px; }
  .contact-row { position: absolute; left: 26px; top: 386px; display: flex; gap: 8px; font-size: 5.2px; color: var(--ink); list-style: none; }
  .contact-row li { display: flex; align-items: center; gap: 2px; }
  .contact-row svg { width: 5px; height: 5px; fill: var(--navy); }
  .letter-body { position: absolute; left: 26px; top: 95px; width: 270px; }
  .salutation { font-size: 6.6px; font-weight: 700; color: var(--heading); margin-bottom: 9px; }
  .letter-body p { font-size: 6.1px; line-height: 9.5px; color: var(--ink); text-align: justify; margin-bottom: 8px; }
  .closing { font-size: 8px; color: #333; margin-top: 4px; }
  .signature { font-family: "Kaushan Script", cursive; font-size: 11px; color: var(--heading); margin-top: 2px; }

  /* Shared footer band */
  .footer-band { position: absolute; left: 0; right: 0; background: var(--navy); color: #fff; font-size: 5px; display: flex; align-items: center; padding-left: 26px; gap: 3px; }
  .footer-band svg { width: 4.5px; height: 4.5px; fill: #fff; }
  .footer-seal { position: absolute; border: 1.6px solid var(--navy); border-radius: 50%; background: var(--paper); }
  .letter .footer-band { top: 404px; height: 8px; }
  .letter .footer-seal { left: 275px; top: 396px; width: 24px; height: 24px; }

  /* Envelopes */
  .envelope { width: 360px; height: 161px; border: 1px solid #d6d6d8; }
  .envelope--back-flap { left: 816px; top: 26px; background: transparent; border: none; overflow: visible; }
  .envelope--back-open { left: 790px; top: 94px; }
  .envelope--front { left: 730px; top: 166px; height: 162px; }
  .envelope svg.flap { position: absolute; left: 0; top: 0; }
  .envelope .brand-ring.solo { position: absolute; }
  .envelope--back-flap .brand-ring.solo { left: 164px; top: 15px; width: 32px; height: 32px; border-color: #fff; background: transparent; }
  .envelope--back-open .brand-ring.solo { left: 159px; top: 29px; width: 40px; height: 40px; }
  .envelope--front .brand { left: 10px; top: 10px; width: 86px; }
  .envelope--front .brand-ring { width: 33px; height: 33px; }
  .envelope--front .brand-name { font-size: 7.6px; }
  .envelope--front .footer-band { top: 177px; top: 142px; height: 8px; padding-left: 8px; }
  .envelope--front .footer-seal { left: 325px; top: 134px; width: 25px; height: 25px; }

  /* Business cards */
  .card { width: 162px; height: 92px; top: 360px; }
  .card--front { left: 736px; }
  .card--back { left: 908px; }
  .card--front .brand { left: 2px; top: 7px; width: 68px; }
  .card--front .brand-ring { width: 22px; height: 22px; }
  .card--front .brand-name { font-size: 5.6px; }
  .person { position: absolute; right: 12px; top: 30px; text-align: right; }
  .person-name { font-size: 6.2px; font-weight: 700; color: var(--navy); }
  .person-role { font-size: 5px; color: var(--ink); }
  .card--front .contact-list { left: 7px; top: 63px; font-size: 4.3px; line-height: 7px; }
  .card--front .contact-list svg { width: 4px; height: 4px; }
  .card--front .footer-band { top: 80px; height: 6px; font-size: 4px; padding-left: 7px; }
  .card--front .footer-seal { left: 130px; top: 73px; width: 20px; height: 20px; }
  .card--back .brand-ring.solo { position: absolute; left: 54px; top: 13px; width: 56px; height: 56px; border-width: 2.6px; }
  .card--back .web { position: absolute; left: 0; right: 0; top: 79px; display: flex; align-items: center; justify-content: center; gap: 5px; font-size: 4.4px; color: var(--ink); letter-spacing: .15em; }
  .card--back .web::before, .card--back .web::after { content: ""; width: 22px; height: .6px; background: var(--ink); }
</style>
</head>
<body>

<svg width="0" height="0" style="position:absolute">
  <defs>
    <symbol id="icon-phone" viewBox="0 0 10 10"><circle cx="5" cy="5" r="5"/><path d="M3 2.5l1 0 .6 1.4-.6.5a4 4 0 0 0 1.6 1.6l.5-.6 1.4.6 0 1a1 1 0 0 1-1 1A5 5 0 0 1 2 3.5a1 1 0 0 1 1-1z" fill="#fff"/></symbol>
    <symbol id="icon-mail" viewBox="0 0 10 10"><rect x="0" y="1.5" width="10" height="7" rx="1"/><path d="M1 2.5l4 3 4-3" stroke="#fff" stroke-width=".9" fill="none"/></symbol>
    <symbol id="icon-web" viewBox="0 0 10 10"><circle cx="5" cy="5" r="5"/><path d="M0 5h10M5 0c-2 3-2 7 0 10M5 0c2 3 2 7 0 10" stroke="#fff" stroke-width=".7" fill="none"/></symbol>
    <symbol id="icon-pin" viewBox="0 0 10 10"><circle cx="5" cy="5" r="5"/><path d="M5 2a2 2 0 0 1 2 2c0 1.5-2 4-2 4S3 5.5 3 4a2 2 0 0 1 2-2z" fill="#2b2f7e"/></symbol>
  </defs>
</svg>

<!-- Letterhead, contacts at top -->
<section class="sheet letter letter--one">
  <div class="brand"><div class="brand-ring"></div><div class="brand-name">Harborline Realty</div></div>
  <ul class="contact-list">
    <li><svg><use href="#icon-phone"/></svg>012-345-6789</li>
    <li><svg><use href="#icon-mail"/></svg>info@harborline.com</li>
    <li><svg><use href="#icon-web"/></svg>www.harborline.com</li>
  </ul>
  <div class="letter-body">
    <p class="salutation">Dear Mr. Lorem,</p>
    <p>Lorem ipsum dolor sit amet, consectetuer adipiscing elit, sed diam nonummy nibh euismod tincidunt ut laoreet dolore magna aliquam erat volutpat. Ut wisi enim ad minim veniam, quis nostrud exerci tation ullamcorper suscipit lobortis nisl ut aliquip ex ea commodo consequat. Duis autem vel eum iriure dolor in hendiusto odio dignissim qui blandit praesent luptatum zzril delenit augue duis dolore te feugait nulla facilisi.</p>
    <p>Lorem ipsum dolor sit amet, consectetuer adipiscing elit, sed diam nonummy nibh euismod tincidunt ut laoreet dolore magna aliquam erat volutpat. Ut wisi enim ad minim veniam, quis nostrud exerci tation ullamcorper suscipit lobortis nisl ut aliquip ex ea commodo consequat. Duis autem vel eum iriure dolor in hendiusto odio dignissim qui blandit praesent luptatum zzril delenit augue duis dolore te feugait nulla facilisi.</p>
    <p>Lorem ipsum dolor sit amet, consectetuer adipiscing elit, sed diam nonummy nibh euismod tincidunt ut laoreet dolore magna aliquam erat volutpat. Ut wisi enim ad minim veniam, quis nostrud exerci tation ullamcorper suscipit lobortis nisl ut aliquip ex ea commodo consequat. Duis autem vel eum iriure dolor in hendiusto odio dignissim qui blandit praesent luptatum zzril delenit augue duis dolore te feugait nulla facilisi.</p>
    <div class="closing">Sincerely Your,</div>
    <div class="signature">Your Name</div>
  </div>
  <div class="footer-band"><svg><use href="#icon-pin"/></svg>Street Name, City Name, Zipcode - 012345</div>
  <div class="footer-seal"></div>
</section>

<!-- Letterhead, contacts at bottom -->
<section class="sheet letter letter--two">
  <div class="brand" style="left:118px"><div class="brand-ring"></div><div class="brand-name">Harborline Realty</div></div>
  <div class="letter-body">
    <p class="salutation">Dear Mr. Lorem,</p>
    <p>Lorem ipsum dolor sit amet, consectetuer adipiscing elit, sed diam nonummy nibh euismod tincidunt ut laoreet dolore magna aliquam erat volutpat. Ut wisi enim ad minim veniam, quis nostrud exerci tation ullamcorper suscipit lobortis nisl ut aliquip ex ea commodo consequat. Duis autem vel eum iriure dolor in hendiusto odio dignissim qui blandit praesent luptatum zzril delenit augue duis dolore te feugait nulla facilisi.</p>
    <p>Lorem ipsum dolor sit amet, consectetuer adipiscing elit, sed diam nonummy nibh euismod tincidunt ut laoreet dolore magna aliquam erat volutpat. Ut wisi enim ad minim veniam, quis nostrud exerci tation ullamcorper suscipit lobortis nisl ut aliquip ex ea commodo consequat. Duis autem vel eum iriure dolor in hendiusto odio dignissim qui blandit praesent luptatum zzril delenit augue duis dolore te feugait nulla facilisi.</p>
    <p>Lorem ipsum dolor sit amet, consectetuer adipiscing elit, sed diam nonummy nibh euismod tincidunt ut laoreet dolore magna aliquam erat volutpat. Ut wisi enim ad minim veniam, quis nostrud exerci tation ullamcorper suscipit lobortis nisl ut aliquip ex ea commodo consequat. Duis autem vel eum iriure dolor in hendiusto odio dignissim qui blandit praesent luptatum zzril delenit augue duis dolore te feugait nulla facilisi.</p>
    <div class="closing">Sincerely Your,</div>
    <div class="signature">Your Name</div>
  </div>
  <ul class="contact-row">
    <li><svg><use href="#icon-phone"/></svg>012-345-6789</li>
    <li><svg><use href="#icon-mail"/></svg>info@harborline.com</li>
    <li><svg><use href="#icon-web"/></svg>www.harborline.com</li>
  </ul>
  <div class="footer-band"><svg><use href="#icon-pin"/></svg>Street Name, City Name, Zipcode - 012345</div>
  <div class="footer-seal"></div>
</section>

<!-- Envelope back, closed navy flap -->
<section class="envelope envelope--back-flap">
  <svg class="flap" width="360" height="161" viewBox="0 0 360 161">
    <rect x="0.5" y="0.5" width="359" height="160" fill="#fff" stroke="#d6d6d8"/>
    <path d="M3 0H357L352 20Q345 30 300 42L190 66Q180 68 170 66L60 42Q15 30 8 20Z" fill="var(--navy)"/>
  </svg>
  <div class="brand-ring solo"></div>
</section>

<!-- Envelope back, outlined flap -->
<section class="envelope envelope--back-open">
  <svg class="flap" width="360" height="161" viewBox="0 0 360 161">
    <path d="M2 0L8 20Q15 30 60 42L170 66Q180 68 190 66L300 42Q345 30 352 20L358 0" fill="none" stroke="#c4c5c8" stroke-width=".8"/>
  </svg>
  <div class="brand-ring solo"></div>
</section>

<!-- Envelope front -->
<section class="envelope envelope--front">
  <div class="brand"><div class="brand-ring"></div><div class="brand-name">Harborline Realty</div></div>
  <div class="footer-band"><svg><use href="#icon-pin"/></svg>Street Name, City Name, Zipcode - 012345</div>
  <div class="footer-seal"></div>
</section>

<!-- Business card front -->
<section class="card card--front">
  <div class="brand"><div class="brand-ring"></div><div class="brand-name">Harborline Realty</div></div>
  <div class="person"><div class="person-name">Dana Whitfield</div><div class="person-role">President</div></div>
  <ul class="contact-list">
    <li><svg><use href="#icon-phone"/></svg>012-345-6789</li>
    <li><svg><use href="#icon-mail"/></svg>info@harborline.com</li>
  </ul>
  <div class="footer-band"><svg><use href="#icon-pin"/></svg>Street Name, City Name, Zipcode - 012345</div>
  <div class="footer-seal"></div>
</section>

<!-- Business card back -->
<section class="card card--back">
  <div class="brand-ring solo"></div>
  <div class="web">www.harborline.com</div>
</section>

</body>
</html>
```